This book will apply the 12 Steps to gaming addiction, also known as video game addiction. The primary purpose of the book is to provide an effective solution for this new type of addiction. The solution is based on the rich and successful concepts of traditional twelve-step programs like RQ.

The title on the cover will be "Nine Doors Out of the Endless Level" and "by Peter Halvorn". A subtitle can be used if it works in your design of "A Practical Path Back from Compulsive Screen Play". Cover will be for a 6" x 9" book approximately 110 pages in length.

Some back cover text including some review quotes and an author bio are in the attached Word doc. There is also an author photo attached for for the back cover.

Requirements
Must have
• For the cover design it could be stylized, or an image, a partial image, or whatever. I am open to suggestions. Think about what would be noticed by a person searching for help with moderating their video game use, or by the parents or loved ones of problem gamers. Something contemporary and eye catching.

```html
<!DOCTYPE html>
<html lang="en">
<head>
<meta charset="utf-8">
<title>Nine Doors Out of the Endless Level — Peter Halvorn</title>
<link rel="stylesheet" href="https://fonts.googleapis.com/css2?family=Michroma&family=Teko:wght@600&display=swap">
<style>
  :root {
    --page-bg: #e6e6e8;
    --cover-magenta: #c8507e;
    --cover-plum: #4a2450;
    --cover-navy: #1c2140;
    --cover-black: #0a0610;
    --title-cream: #f1ebdf;
    --title-cyan: #2bb9de;
  }
  html, body {
    margin: 0;
    padding: 0;
    width: 1179px;
    height: 1200px;
    overflow: hidden;
    background: var(--page-bg);
  }
  .canvas {
    position: relative;
    width: 1179px;
    height: 1200px;
  }
  .book-cover {
    position: absolute;
    left: 202px;
    top: 30px;
    width: 775px;
    height: 1140px;
    box-shadow: 0 18px 40px rgba(0, 0, 0, 0.25);
  }
  .book-cover svg {
    display: block;
    width: 100%;
    height: 100%;
  }
  .author-name {
    font-family: "Michroma", sans-serif;
    font-size: 27px;
    letter-spacing: 5px;
    fill: var(--title-cream);
  }
  .title-line {
    font-family: "Teko", sans-serif;
    font-weight: 600;
    text-transform: uppercase;
  }
  .title-line--small { font-size: 175px; fill: var(--title-cream); }
  .title-line--large { font-size: 290px; fill: var(--title-cream); }
  .title-line--accent { fill: var(--title-cyan); }
</style>
</head>
<body>
<main class="canvas">
  <section class="book-cover">
    <svg viewBox="0 0 775 1140" xmlns="http://www.w3.org/2000/svg">
      <defs>
        <linearGradient id="coverBase" x1="0" y1="0" x2="1" y2="0.35">
          <stop offset="0" stop-color="var(--cover-magenta)"/>
          <stop offset="0.35" stop-color="var(--cover-plum)"/>
          <stop offset="0.7" stop-color="var(--cover-navy)"/>
          <stop offset="1" stop-color="var(--cover-black)"/>
        </linearGradient>
        <radialGradient id="coverGlow" cx="0.35" cy="0.45" r="0.5">
          <stop offset="0" stop-color="#2a3f7a" stop-opacity="0.55"/>
          <stop offset="1" stop-color="#2a3f7a" stop-opacity="0"/>
        </radialGradient>
        <linearGradient id="coverShade" x1="0" y1="0" x2="1" y2="0">
          <stop offset="0.55" stop-color="#000" stop-opacity="0"/>
          <stop offset="1" stop-color="#000" stop-opacity="0.55"/>
        </linearGradient>
      </defs>
      <g role="img" aria-label="Glowing digital network of connected nodes over a magenta-to-navy gradient">
        <rect class="cover-background" width="775" height="1140" fill="url(#coverBase)"/>
        <rect width="775" height="1140" fill="url(#coverGlow)"/>
        <rect width="775" height="1140" fill="url(#coverShade)"/>
      </g>

      <text class="author-name" x="387.5" y="70" text-anchor="middle">PETER HALVORN</text>

      <text class="title-line title-line--small" x="104" y="330" textLength="566" lengthAdjust="spacingAndGlyphs">Nine Doors</text>
      <text class="title-line title-line--small" x="104" y="475" textLength="566" lengthAdjust="spacingAndGlyphs">Out of the</text>
      <text class="title-line title-line--large" x="104" y="705" textLength="566" lengthAdjust="spacingAndGlyphs">Endless</text>
      <text class="title-line title-line--large title-line--accent" x="104" y="935" textLength="566" lengthAdjust="spacingAndGlyphs">Level</text>
    </svg>
  </section>
</main>
</body>
</html>
```